Patent Law

Need to develop a home page for a patent lawyer.

Colors should go with logo, blues...

Company Name- Velun Tresk, PLLC

Company Overview-

I am an Intellectual Property Lawyer and focus on patents, copyrights, trademarks, & trade secrets. I work with small businesses and start ups in the chemical and biotech industries.

Why Us-

I am small firm that can provide large-firm service at a reasonable price. I also can charge flat-fees for entreprenuers in certain practice areas.

Services-
Intellectual Property
Patents
Copyrights
Trademarks
Trade secrets
Healthcare Compliance
Elder law
Wills
Trusts

Website we like-
http://www.quorvantlegal.example/ - within industry!!
http://www.daltrowemiko.example/
http://ulbrixtane.example/
http://thegravelcounsel.example/

Target Market(s)

My customers will be small business, specifically small start-up companies in the chemical and biotech arena.

Industry/Entity Type

Trade

Requirements
Must have
• Colors should go with logo, blues...

```html
<!DOCTYPE html>
<html lang="en">
<head>
<meta charset="utf-8">
<title>Velun Tresk, PLLC – Patent Law Firm</title>
<link href="https://fonts.googleapis.com/css2?family=Montserrat:wght@300;400;600;700&family=Mulish:ital,wght@0,300;0,400;0,600;0,700;1,300;1,400&display=swap" rel="stylesheet">
<style>
:root{
  --blue:#1a8ad4;
  --blue-dark:#0f6fb3;
  --blue-btn-top:#1aa0e8;
  --blue-btn-bottom:#0a6fc0;
  --ink:#1b1b1b;
  --text:#444;
  --muted:#7a7a7a;
  --page:#ececec;
  --rule:#d2d2d2;
  --white:#ffffff;
  --hero-warm:#6b4a24;
  --hero-deep:#1a130c;
}
*{margin:0;padding:0;box-sizing:border-box}
html,body{width:894px;height:1200px;overflow:hidden}
body{font-family:"Mulish",Arial,sans-serif;background:var(--page);color:var(--text);position:relative}
a{color:inherit;text-decoration:none}

/* Hero */
.hero{position:absolute;left:0;top:0;width:894px;height:472px;overflow:hidden}
.hero-photo{position:absolute;inset:0;display:block}
.brand{position:absolute;left:78px;top:40px;display:flex;align-items:center;gap:8px}
.brand-dot{width:14px;height:14px;border-radius:50%;background:var(--blue)}
.brand-name{font-family:"Mulish",sans-serif;font-weight:700;font-size:13px;color:var(--white);letter-spacing:.5px;text-transform:uppercase}
.main-nav{position:absolute;left:254px;top:74px;display:flex;gap:0;font-size:11.5px;color:var(--white)}
.main-nav a{padding:4px 7px;margin-right:18px;line-height:13px}
.main-nav a.active{background:var(--blue);border-radius:2px}
.quick-contact{position:absolute;left:614px;top:0;width:181px;height:143px;background:var(--blue);border:2px solid var(--blue)}
.quick-contact .map{display:block;width:177px;height:98px;background:linear-gradient(135deg,#e9e6df,#d8d6cf)}
.quick-contact .ask{font-size:10px;color:#cfe8fa;margin:4px 0 0 3px}
.quick-contact .ask b{font-weight:600;color:#e6f4ff}
.quick-contact .line{display:flex;align-items:center;margin:2px 0 0 3px;color:var(--white)}
.quick-contact .phone{font-family:"Montserrat",sans-serif;font-weight:700;font-size:14px}
.quick-contact .or{font-size:10px;color:#cfe8fa;margin:0 8px 0 11px}
.quick-contact .mail{font-size:8px;font-weight:600;display:flex;align-items:center;gap:3px}
.hero-copy{position:absolute;left:0;width:894px;top:190px;text-align:center;color:var(--white)}
.hero-copy h1{font-family:"Montserrat",sans-serif;font-weight:700;font-size:60px;line-height:66px;letter-spacing:-1px;text-shadow:0 2px 6px rgba(0,0,0,.45)}
.hero-copy .tagline{font-family:"Montserrat",sans-serif;font-weight:300;font-size:42px;line-height:44px}
.hero-copy p{width:480px;margin:10px auto 0;font-size:14.5px;line-height:18px;font-weight:400;text-shadow:0 1px 3px rgba(0,0,0,.5)}

/* Feature columns */
.features{position:absolute;top:510px;left:118px;display:flex;gap:43px}
.feature{width:191px;text-align:center}
.feature .frame{width:191px;height:115px;border:3px solid #c9c9c9;background:#fff}
.feature .photo{display:block;width:100%;height:100%}
.feature h2{font-family:"Montserrat",sans-serif;font-weight:600;font-size:14.5px;color:var(--ink);margin-top:19px;letter-spacing:.3px}
.feature .sub{font-style:italic;font-weight:300;font-size:11px;color:var(--muted);margin-top:1px}
.feature .body{font-size:8.6px;line-height:13.5px;color:#333;margin-top:8px}
.feature .body b{color:#111;font-weight:700}
.feature .body a{color:var(--blue)}
.divider{position:absolute;top:796px;left:40px;width:814px;height:14px;background:radial-gradient(ellipse at top,rgba(0,0,0,.14),rgba(0,0,0,0) 70%)}

/* Contact call-out */
.callout{position:absolute;top:870px;left:0;width:894px;text-align:center}
.callout h2{font-family:"Montserrat",sans-serif;font-weight:300;font-size:29px;color:var(--blue);letter-spacing:-.2px}
.callout p{width:370px;margin:12px auto 0;font-size:11px;line-height:19px;color:#666}
.social{position:absolute;top:970px;left:197px;width:500px;height:39px;border-top:1px solid var(--rule);border-bottom:1px solid var(--rule);display:flex;align-items:center}
.social-item{display:flex;align-items:center;gap:6px;position:absolute}
.social-item .ring{width:24px;height:24px;border-radius:50%;border:2px solid currentColor}
.social-item .label{font-size:8px;font-weight:700;font-style:italic;line-height:9px}
.social-item .handle{font-size:7.3px;color:#555;font-weight:400;font-style:normal}
.fan{left:12px;color:#2c4a8a}
.tweet{left:156px;color:#2bb0e8}
.follow{left:233px;color:#777}
.follow .ring{border-color:#e4e4e4}
.connect{left:359px;color:#1a5f9e}
.hours{position:absolute;top:1043px;left:0;width:894px;display:flex;justify-content:center;align-items:baseline;gap:22px;font-size:11px;color:#555}
.hours b{font-family:"Montserrat",sans-serif;font-weight:600;font-size:15px;color:var(--blue)}
.send-btn{position:absolute;left:373px;top:1072px;width:147px;height:39px;border-radius:2px;background:linear-gradient(var(--blue-btn-top),var(--blue-btn-bottom));border-bottom:2px solid #075a9c;color:var(--white);font-family:"Montserrat",sans-serif;font-weight:600;font-size:14px;display:flex;align-items:center;justify-content:center}

/* Footer */
.site-footer{position:absolute;top:1135px;left:74px;width:746px;border-top:1px solid var(--rule)}
.site-footer .copy{position:absolute;left:56px;top:27px;font-size:9.5px;color:#333}
.footer-nav{position:absolute;left:298px;top:27px;display:flex;font-size:9.5px;color:#333}
.footer-nav a{padding:0 13px;border-left:1px solid #555;line-height:12px}
.footer-nav a:first-child{border-left:0;padding-left:0;color:var(--blue)}
.bottom-bar{position:absolute;left:0;top:1195px;width:894px;height:5px;background:var(--blue)}
</style>
</head>
<body>

<header class="hero">
  <svg class="hero-photo" width="894" height="472" viewBox="0 0 894 472" role="img" aria-label="Photo of brass scales of justice in a wood-panelled courtroom">
    <defs>
      <radialGradient id="warm" cx="0.3" cy="0.45" r="0.8">
        <stop offset="0" stop-color="#b0844c"/>
        <stop offset="0.5" stop-color="#6b4a24"/>
        <stop offset="1" stop-color="#2a1d10"/>
      </radialGradient>
      <linearGradient id="shade" x1="0" y1="0" x2="1" y2="0">
        <stop offset="0" stop-color="#1a130c" stop-opacity=".55"/>
        <stop offset="1" stop-color="#120d08" stop-opacity=".9"/>
      </linearGradient>
    </defs>
    <rect width="894" height="472" fill="url(#warm)"/>
    <polygon points="260,0 894,0 894,472 530,472" fill="url(#shade)"/>
  </svg>

  <a class="brand" href="#"><span class="brand-dot"></span><span class="brand-name">Velun Tresk, PLLC</span></a>

  <nav class="main-nav">
    <a class="active" href="#">Home</a>
    <a href="#">About</a>
    <a href="#">Resources</a>
    <a href="#">Practice Areas</a>
  </nav>

  <aside class="quick-contact">
    <svg class="map" role="img" aria-label="Street map of the office location"></svg>
    <div class="ask"><b>Any Questions?</b> Please Call</div>
    <div class="line">
      <span class="phone">888-555-0142</span><span class="or">OR</span>
      <span class="mail"><svg width="12" height="9" viewBox="0 0 12 9"><rect x=".5" y=".5" width="11" height="8" fill="none" stroke="#fff"/><path d="M.5 .5 6 5 11.5 .5" fill="none" stroke="#fff"/></svg>Mail Us</span>
    </div>
  </aside>

  <div class="hero-copy">
    <h1>Velun Tresk</h1>
    <div class="tagline">Paten Law Firm</div>
    <p>I am an Intellectual Property Lawyer and focus on patents, copyrights, trademarks, &amp; trade secrets. I work with small businesses and start ups in the chemical and biotech industries.</p>
  </div>
</header>

<section class="features">
  <article class="feature">
    <div class="frame"><svg class="photo" role="img" aria-label="Photo of a hand holding a wooden gavel" style="background:radial-gradient(circle at 40% 40%,#8a6a4c,#2a1c12)"></svg></div>
    <h2>WHY US?</h2>
    <div class="sub">This is a reason why you choose us</div>
    <p class="body">I am small firm that can provide large-firm service at a reasonable price. I also can charge flat-fees for entreprenuers in certain practice areas.</p>
  </article>
  <article class="feature">
    <div class="frame"><svg class="photo" role="img" aria-label="Photo of a gavel resting in front of an open law book" style="background:linear-gradient(135deg,#c8a67e,#6b4628 60%,#2d1a0e)"></svg></div>
    <h2>WHAT WE DO</h2>
    <div class="sub">What can we do for you?</div>
    <p class="body">Intellectual Property &nbsp;|&nbsp; Patents &nbsp;|&nbsp; Copyrights<br>Trademarks &nbsp;|&nbsp; Trade secrets &nbsp;|&nbsp; Healthcare<br>Compliance &nbsp;|&nbsp; Elder law &nbsp;|&nbsp; Wills &nbsp;|&nbsp; Trusts</p>
  </article>
  <article class="feature">
    <div class="frame"><svg class="photo" role="img" aria-label="Photo of a wooden gavel on its sound block" style="background:radial-gradient(circle at 60% 45%,#c58a44,#4a2a12 70%,#1e1007)"></svg></div>
    <h2>CONTACT INFO</h2>
    <div class="sub">Where you can find us?</div>
    <p class="body">212th ST. Larkmoor - Fenwick Park, KANSAS<br>MISSOURI 55810</p>
    <p class="body" style="margin-top:9px">Phone. <b>888-555-0142</b><br>Email. <a href="#">client@veluntresk.example</a></p>
  </article>
</section>

<div class="divider"></div>

<section class="callout">
  <h2>Velun Tresk - Patent Lawyer.</h2>
  <p>For business consultation and information of your patents, please contact us. We are ready to serve you.</p>
</section>

<nav class="social">
  <a class="social-item fan" href="#"><span class="ring"></span><span class="label">BECOME FAN<br><span class="handle">fanpage.example/veluntresk</span></span></a>
  <a class="social-item tweet" href="#"><span class="ring"></span><span class="label">TWEET<br><span class="handle" style="color:#2bb0e8">@veluntresk</span></span></a>
  <a class="social-item follow" href="#"><span class="ring"></span><span class="label">FOLLOW<br><span class="handle">circles.example/veluntresk</span></span></a>
  <a class="social-item connect" href="#"><span class="ring"></span><span class="label">CONNECT<br><span class="handle" style="color:#1a5f9e">profiles.example/in/veluntresk</span></span></a>
</nav>

<div class="hours">
  <span>Open <b>08am - 16pm</b></span>
  <span>Appointment <b>888-555-0142</b></span>
</div>
<a class="send-btn" href="#">SEND US EMAIL</a>

<footer class="site-footer">
  <div class="copy">Velun Tresk | © 2014 All Right Reserved</div>
  <nav class="footer-nav">
    <a href="#">Home</a>
    <a href="#">Pricing</a>
    <a href="#">Resource</a>
    <a href="#">Terms &amp; Condition</a>
    <a href="#">Privacy Policy</a>
    <a href="#">Fees</a>
  </nav>
</footer>
<div class="bottom-bar"></div>

</body>
</html>
```